Brisk Fixwell business card

I need business card for my business, I think you have all my details.six months ago I design with you car wrap design. We would like to design both side of the card. On front of card we would like logo , Name and our contact details.
At the back we are looking to mentioned our services.
The name will be:
Faridoullan Mestor
Managing Director
Ph:07952338417
Email:info@brisk-fixwell.com
Web:www.brisk-fixwell.com
So we have our logo, you don’t need to change the logo.
Please see the attachment.
Thanks

Target Market(s)

Home improvement

Industry/Entity Type

Home Improvement

Contact Information for Business Card

Company name: Brisk Fixwell
Name: Faridoullan Mestor
Position: Director
Ph:07952338417
Web: www.brisk-fixwell.com
Add: 42 Corvale Road
Hounslow
TW3 9KD
SECOND PERSON
Nizamuddel mestor
Position: Handyman
Ph: 07812 564037
Email: info@brisk-fixwell.com
Add: 18 Brackwin Lane Road
Hounslow
TW6 2LB

```html
<!DOCTYPE html>
<html lang="en">
<head>
<meta charset="UTF-8">
<title>Brisk Fixwell – Business Card</title>
<link rel="stylesheet" href="https://fonts.googleapis.com/css2?family=Roboto:wght@400;700&family=Saira+Semi+Condensed:wght@600&display=swap">
<style>
  :root {
    --navy: #22245e;
    --navy-faint: #3a3d7a;
    --red: #b71f1c;
    --paper: #f4f4f4;
    --ink: #2b2b2b;
    --backdrop: #c4c4c4;
    --band-text: #f2e6e6;
  }
  * { margin: 0; padding: 0; box-sizing: border-box; }
  html, body { width: 1200px; height: 576px; overflow: hidden; }
  body {
    background: var(--backdrop);
    position: relative;
    font-family: "Roboto", sans-serif;
  }
  .card {
    position: absolute;
    width: 484px;
    height: 292px;
    top: 139px;
    border-radius: 10px;
    overflow: hidden;
  }
  /* Services side */
  .card--services { left: 82px; background: var(--navy); }
  .services-mark {
    position: absolute;
    top: 72px; left: 0; width: 100%;
    text-align: center;
  }
  .services-mark__name {
    font-family: "Roboto", sans-serif;
    font-weight: 700;
    font-size: 30px;
    color: var(--navy-faint);
    letter-spacing: 0.5px;
  }
  .services-band {
    position: absolute;
    left: 0; bottom: 0;
    width: 100%; height: 46px;
    background: var(--red);
    color: var(--band-text);
    font-size: 13px;
    line-height: 15.5px;
    text-align: center;
    padding-top: 8px;
  }
  /* Contact side */
  .card--contact { left: 602px; background: var(--paper); }
  .brand {
    position: absolute;
    left: 36px; top: 130px;
    display: flex; align-items: center; gap: 10px;
  }
  .brand__name {
    font-family: "Roboto", sans-serif;
    font-weight: 700;
    font-size: 28px;
    color: var(--navy);
  }
  .brand__dot {
    width: 22px; height: 22px;
    border-radius: 50%;
    background: var(--navy);
  }
  .person { position: absolute; left: 274px; top: 86px; }
  .person__name {
    font-family: "Saira Semi Condensed", sans-serif;
    font-weight: 600;
    font-size: 18px;
    color: var(--navy);
    line-height: 22px;
  }
  .person__role { font-size: 12.5px; color: var(--ink); margin-top: 1px; }
  .contacts {
    position: absolute; left: 280px; top: 148px;
    list-style: none;
  }
  .contacts li {
    display: flex; align-items: center; gap: 11px;
    font-size: 12.5px; color: var(--ink);
    height: 18.5px;
  }
  .contacts svg { width: 10px; height: 10px; fill: var(--red); }
  .edge-bar {
    position: absolute; left: 0; bottom: 0;
    width: 100%; height: 6px; display: flex;
  }
  .edge-bar__navy { width: 50%; background: var(--navy); }
  .edge-bar__red { width: 50%; background: var(--red); }
</style>
</head>
<body>
  <section class="card card--services">
    <div class="services-mark"><span class="services-mark__name">Brisk Fixwell</span></div>
    <div class="services-band">
      <p>Electrical &nbsp;|&nbsp; Carpentry &nbsp;|&nbsp; Plumbing &nbsp;|&nbsp; Plastering &nbsp;|&nbsp; Flooring</p>
      <p>Fencing &nbsp;|&nbsp; Decking &nbsp;|&nbsp; Painting &amp; Decorating</p>
    </div>
  </section>

  <section class="card card--contact">
    <div class="brand">
      <span class="brand__name">Brisk Fixwell</span>
      <span class="brand__dot"></span>
    </div>
    <div class="person">
      <p class="person__name">Faridoullan Mestor</p>
      <p class="person__role">Managing Director</p>
    </div>
    <ul class="contacts">
      <li>
        <svg viewBox="0 0 10 10" aria-hidden="true"><path d="M1 3 Q5 0 9 3 L8 4.5 L6.5 4 L6.5 3.2 Q5 2.6 3.5 3.2 L3.5 4 L2 4.5 Z M2.5 5 H7.5 L8.5 9 H1.5 Z"/></svg>
        07952338417
      </li>
      <li>
        <svg viewBox="0 0 10 10" aria-hidden="true"><path d="M0 2 H10 V8.5 H0 Z" /><path d="M0.5 2.4 L5 5.8 L9.5 2.4" stroke="#f4f4f4" stroke-width="0.9" fill="none"/></svg>
        info@brisk-fixwell.com
      </li>
      <li>
        <svg viewBox="0 0 10 10" aria-hidden="true"><circle cx="5" cy="5" r="4.5"/><path d="M0.5 5 H9.5 M5 0.5 V9.5 M5 0.5 Q2 5 5 9.5 M5 0.5 Q8 5 5 9.5" stroke="#f4f4f4" stroke-width="0.7" fill="none"/></svg>
        www.brisk-fixwell.com
      </li>
    </ul>
    <div class="edge-bar"><span class="edge-bar__navy"></span><span class="edge-bar__red"></span></div>
  </section>
</body>
</html>
```